GJ & DW Fencing Pty Ltd

We already have an existing logo created by Pixel Harbour however we have restructured to a company. We would like someone to add Pty Ltd to our business name please.

Colors

Designer to choose only greyscale colors for use in the design.

```html
<!DOCTYPE html>
<html lang="en">
<head>
<meta charset="utf-8">
<title>GJ &amp; DW Fencing Pty Ltd – Business Card</title>
<link rel="stylesheet" href="https://fonts.googleapis.com/css2?family=Lora:wght@400;700&display=swap">
<style>
  :root {
    --page-bg: #d9d9d9;
    --card-dark: #161616;
    --card-light: #ffffff;
    --ink-dark: #1c1c1c;
    --ink-mid: #3a3a3a;
    --ink-light: #f4f4f4;
    --rule: #8a8a8a;
  }
  * { box-sizing: border-box; margin: 0; padding: 0; }
  html, body { width: 1200px; height: 800px; overflow: hidden; }
  body {
    background: var(--page-bg);
    font-family: "Lora", Georgia, serif;
    display: flex;
    align-items: center;
    justify-content: center;
    gap: 48px;
  }
  .card {
    width: 525px;
    height: 300px;
    position: relative;
    box-shadow: 0 10px 28px rgba(0,0,0,0.25);
  }
  .card--back {
    background: var(--card-dark);
    display: flex;
    align-items: center;
    justify-content: center;
  }
  .card--front { background: var(--card-light); color: var(--ink-dark); }

  .wordmark {
    font-weight: 700;
    text-transform: uppercase;
    line-height: 1;
    text-align: center;
  }
  .wordmark__main { display: block; font-size: 46px; letter-spacing: 1px; }
  .wordmark__sub { display: block; font-size: 22px; letter-spacing: 3px; margin-top: 6px; }
  .card--back .wordmark { color: var(--ink-light); }
  .card--front .wordmark {
    color: var(--ink-dark);
    position: absolute;
    top: 46px;
    left: 0;
    right: 0;
  }

  .card__details {
    position: absolute;
    left: 0;
    right: 0;
    top: 168px;
    display: flex;
    align-items: stretch;
  }
  .person {
    width: 50%;
    padding-right: 22px;
    text-align: right;
    display: flex;
    flex-direction: column;
    justify-content: flex-end;
    padding-bottom: 4px;
  }
  .person__name { font-weight: 700; font-size: 15px; letter-spacing: 0.5px; text-transform: uppercase; }
  .person__role { font-size: 13px; color: var(--ink-mid); margin-top: 2px; }
  .divider { width: 1px; background: var(--rule); height: 96px; }
  .contact {
    padding-left: 22px;
    font-size: 12px;
    line-height: 1.6;
    color: var(--ink-mid);
    list-style: none;
  }
  .contact__item { display: flex; align-items: center; gap: 7px; }
  .contact__item--plain { padding-left: 21px; }
  .contact__company { font-weight: 700; color: var(--ink-dark); }
  .contact__icon { width: 14px; height: 14px; flex: none; }
</style>
</head>
<body>
  <section class="card card--back" aria-label="Card back">
    <p class="wordmark">
      <span class="wordmark__main">GJ &amp; DW</span>
      <span class="wordmark__sub">Fencing Pty Ltd</span>
    </p>
  </section>

  <section class="card card--front" aria-label="Card front">
    <p class="wordmark">
      <span class="wordmark__main">GJ &amp; DW</span>
      <span class="wordmark__sub">Fencing Pty Ltd</span>
    </p>
    <div class="card__details">
      <div class="person">
        <p class="person__name">Liam Carter</p>
        <p class="person__role">President</p>
      </div>
      <div class="divider"></div>
      <ul class="contact">
        <li class="contact__item">
          <svg class="contact__icon" viewBox="0 0 14 14" aria-hidden="true">
            <circle cx="7" cy="7" r="7" fill="#2a2a2a"/>
            <rect x="4.5" y="3" width="5" height="8" rx="1" fill="#fff"/>
            <rect x="5.3" y="4" width="3.4" height="5" fill="#2a2a2a"/>
          </svg>
          Ned 0412558019
        </li>
        <li class="contact__item">
          <svg class="contact__icon" viewBox="0 0 14 14" aria-hidden="true">
            <circle cx="7" cy="7" r="7" fill="#2a2a2a"/>
            <rect x="3.5" y="4.5" width="7" height="5" fill="#fff"/>
            <path d="M3.5 4.5 L7 7.3 L10.5 4.5" fill="none" stroke="#2a2a2a" stroke-width="0.8"/>
          </svg>
          office@gjdwfencing.com.au
        </li>
        <li class="contact__item contact__item--plain contact__company">GJ &amp; DW Fencing Pty Ltd</li>
        <li class="contact__item contact__item--plain">PO Box 418 Carrow WA 6512</li>
      </ul>
    </div>
  </section>
</body>
</html>
```